Retail Jewelry Business Card Design Project

We are in need of a new business card design for a retail jewelry store. This store is in the business of fine jewelry including but not specific to bridal jewelry, diamonds, designer jewelry and watches.

This store has been in business for 20 years but continues to strive for a modern professional appeal. The main colors use for this business are a royal blue, white and silver.

Target Market(s)

Target market is ages 18-50

Industry/Entity Type

Jewelry

Requirements
Must have
• Sales Person Name
Sales Person Email Address

Store Address
Store Phone
Website

Standard business card size. No odd shapes or sizes.
Nice to have
• Overall modern feel for card.

We have thought that a design with a nice feature of the logo on the back of the card would be nice but open to ideas.
Should not have
• No specific images of jewelry should be used.

```html
<!DOCTYPE html>
<html lang="en">
<head>
<meta charset="utf-8">
<title>Marlow Reed Fine Jewelry – Business Cards</title>
<link rel="stylesheet" href="https://fonts.googleapis.com/css2?family=Jost:wght@400;500&display=swap">
<style>
  :root {
    --royal-blue: #2e3590;
    --lavender-rule: #7b74b8;
    --card-white: #ffffff;
    --backdrop: #eceef3;
    --shadow: rgba(20, 24, 60, 0.18);
  }
  * { box-sizing: border-box; margin: 0; padding: 0; }
  html, body {
    width: 1200px;
    height: 700px;
    overflow: hidden;
    background: var(--backdrop);
    font-family: "Jost", "Futura", sans-serif;
  }
  .canvas {
    position: relative;
    width: 1200px;
    height: 700px;
  }
  .card {
    position: absolute;
    top: 200px;
    width: 525px;
    height: 300px;
    box-shadow: 0 10px 28px var(--shadow);
    overflow: hidden;
  }
  .card--front { left: 60px; background: var(--card-white); }
  .card--back {
    left: 615px;
    background: var(--royal-blue);
    color: var(--card-white);
    display: flex;
    flex-direction: column;
    align-items: center;
    justify-content: center;
  }

  /* Front card */
  .band {
    position: absolute;
    left: 0;
    width: 100%;
    background: var(--royal-blue);
    color: var(--card-white);
    display: flex;
    align-items: center;
    justify-content: center;
  }
  .band--top {
    top: 0;
    height: 52px;
    padding-top: 4px;
  }
  .band--bottom {
    bottom: 0;
    height: 40px;
    padding-bottom: 2px;
  }
  .band__rule {
    position: absolute;
    left: 0;
    width: 100%;
    height: 2px;
    background: var(--lavender-rule);
  }
  .band--top .band__rule { bottom: 6px; background: var(--card-white); height: 1px; }
  .rule-under-top { position: absolute; top: 52px; left: 0; width: 100%; height: 3px; background: var(--lavender-rule); }
  .rule-over-bottom { position: absolute; bottom: 40px; left: 0; width: 100%; height: 3px; background: var(--lavender-rule); }
  .band--bottom .band__rule { top: 5px; background: var(--card-white); height: 1px; }

  .sales-name {
    font-size: 20px;
    font-weight: 400;
    letter-spacing: 1.5px;
    text-transform: uppercase;
  }
  .store-address {
    font-size: 14px;
    letter-spacing: 1px;
    margin-top: 6px;
  }

  .store-name {
    position: absolute;
    top: 86px;
    left: 0;
    width: 100%;
    text-align: center;
    color: var(--royal-blue);
    font-weight: 500;
  }
  .store-name__main {
    display: block;
    font-size: 50px;
    line-height: 1;
    letter-spacing: 1px;
  }
  .store-name__sub {
    display: block;
    font-size: 22px;
    letter-spacing: 4px;
    text-transform: uppercase;
    margin-top: 6px;
  }

  .contact-row {
    position: absolute;
    top: 208px;
    left: 0;
    width: 100%;
    display: flex;
    justify-content: center;
    gap: 18px;
    color: var(--royal-blue);
    font-size: 14px;
    letter-spacing: 0.3px;
  }
  .contact-item { display: flex; align-items: center; gap: 6px; }
  .contact-icon { width: 12px; height: 12px; fill: var(--royal-blue); }

  /* Back card */
  .back-name {
    text-align: center;
    font-weight: 500;
  }
  .back-name__main {
    display: block;
    font-size: 56px;
    line-height: 1;
    letter-spacing: 1px;
  }
  .back-name__sub {
    display: block;
    font-size: 24px;
    letter-spacing: 5px;
    text-transform: uppercase;
    margin-top: 8px;
  }
  .website {
    margin-top: 34px;
    font-size: 15px;
    letter-spacing: 2.5px;
  }
</style>
</head>
<body>
<main class="canvas">
  <section class="card card--front" aria-label="Business card front">
    <div class="band band--top">
      <span class="sales-name">Marlow Reed Ashford</span>
      <span class="band__rule"></span>
    </div>
    <div class="rule-under-top"></div>

    <h1 class="store-name">
      <span class="store-name__main">Marlow Reed</span>
      <span class="store-name__sub">Fine Jewelry</span>
    </h1>

    <div class="contact-row">
      <span class="contact-item">
        <svg class="contact-icon" viewBox="0 0 24 24" aria-hidden="true"><path d="M6.6 10.8a15.2 15.2 0 0 0 6.6 6.6l2.2-2.2a1 1 0 0 1 1-.25 11.4 11.4 0 0 0 3.6.57 1 1 0 0 1 1 1V20a1 1 0 0 1-1 1A17 17 0 0 1 3 4a1 1 0 0 1 1-1h3.5a1 1 0 0 1 1 1c0 1.25.2 2.45.57 3.57a1 1 0 0 1-.25 1z"/></svg>
        555-204-7731
      </span>
      <span class="contact-item">
        <svg class="contact-icon" viewBox="0 0 24 24" aria-hidden="true"><path d="M2 5h20v14H2z M3 6l9 7 9-7" fill="none" stroke="currentColor"/><path d="M2 5h20v14H2zm2 2v.3l8 6.2 8-6.2V7l-8 6.2z"/></svg>
        marlow@marlowreedjewelry.com
      </span>
    </div>

    <div class="rule-over-bottom"></div>
    <div class="band band--bottom">
      <span class="band__rule"></span>
      <span class="store-address">872 Linden Avenue, Harbor Bay, FL 32490</span>
    </div>
  </section>

  <section class="card card--back" aria-label="Business card back">
    <h2 class="back-name">
      <span class="back-name__main">Marlow Reed</span>
      <span class="back-name__sub">Fine Jewelry</span>
    </h2>
    <p class="website">www.marlowreedjewelry.com</p>
  </section>
</main>
</body>
</html>
```